Investment company needing business card

We are wanting a business card which looks sharp and easy on the eye. We are thinking of having a business card with the logo embossed on it, to really make it stand out. We will only have a small amount of information of the business card, person's name, position, email address and phone number

Contact Information for Business Card

Danielle Frost
Executive Assistant
+64 21 473 5162
danielf@harwickpartners.co.nz

Requirements
Must have
• Embossed logo
Should not have
• Not to be busy

```html
<!DOCTYPE html>
<html lang="en">
<head>
<meta charset="utf-8">
<title>Harwick Partners – Business Card</title>
<link href="https://fonts.googleapis.com/css2?family=Lato:wght@400;700&display=swap" rel="stylesheet">
<style>
  :root {
    --backdrop: #17191b;
    --card: #262c2d;
    --green: #22b573;
    --cream: #ebe6dc;
    --white: #ffffff;
    --muted: #dfe3e2;
  }
  * { box-sizing: border-box; margin: 0; padding: 0; }
  html, body {
    width: 1200px;
    height: 800px;
    overflow: hidden;
    background: var(--backdrop);
    font-family: "Lato", sans-serif;
  }
  .stage {
    width: 1200px;
    height: 800px;
    display: flex;
    align-items: center;
    justify-content: center;
    gap: 40px;
  }
  .card {
    position: relative;
    width: 540px;
    height: 309px;
    background: var(--card);
    overflow: hidden;
    box-shadow: 0 18px 40px rgba(0,0,0,.55);
  }
  .edge-band {
    position: absolute;
    left: 0; right: 0; bottom: 0;
    height: 9px;
    display: flex;
  }
  .edge-band .green { flex: 0 0 62%; background: var(--green); }
  .edge-band .cream { flex: 1; background: var(--cream); }

  .brand {
    position: absolute;
    display: flex;
    align-items: center;
    gap: 12px;
    color: var(--green);
    font-weight: 700;
    letter-spacing: 2px;
    text-transform: uppercase;
    white-space: nowrap;
  }
  .brand .mark {
    width: 34px;
    height: 34px;
    background: var(--green);
  }
  .card-front .brand {
    left: 50%;
    top: 50%;
    transform: translate(-50%, -60%);
    font-size: 30px;
  }
  .card-back .brand {
    left: 50px;
    top: 70px;
    font-size: 26px;
  }
  .card-back .brand .mark { width: 30px; height: 30px; }

  .contact {
    position: absolute;
    left: 50px;
    bottom: 44px;
    color: var(--muted);
  }
  .contact .name {
    color: var(--green);
    font-size: 19px;
    font-weight: 700;
    line-height: 1.1;
  }
  .contact .role {
    font-size: 14px;
    color: var(--white);
    margin-bottom: 16px;
  }
  .contact .line {
    display: flex;
    align-items: center;
    gap: 10px;
    font-size: 13px;
    line-height: 1.7;
  }
  .contact svg { width: 13px; height: 13px; flex: none; }
</style>
</head>
<body>
<main class="stage">
  <section class="card card-front" aria-label="Business card front">
    <div class="brand"><span class="mark"></span>Harwick Partners</div>
    <div class="edge-band"><span class="green"></span><span class="cream"></span></div>
  </section>

  <section class="card card-back" aria-label="Business card back">
    <div class="brand"><span class="mark"></span>Harwick Partners</div>
    <div class="contact">
      <p class="name">Danielle Frost</p>
      <p class="role">Executive Assistant</p>
      <p class="line">
        <svg viewBox="0 0 13 13" aria-hidden="true"><rect x="1.5" y="1.5" width="10" height="10" fill="none" stroke="#22b573" stroke-width="1.5"/></svg>
        +64 21 473 5162
      </p>
      <p class="line">
        <svg viewBox="0 0 13 13" aria-hidden="true"><rect x="1" y="2.5" width="11" height="8" fill="#22b573"/><path d="M1 2.5 L6.5 7 L12 2.5" fill="none" stroke="#262c2d" stroke-width="1.2"/></svg>
        danielf@harwickpartners.co.nz
      </p>
    </div>
    <div class="edge-band"><span class="green"></span><span class="cream"></span></div>
  </section>
</main>
</body>
</html>
```